Wordpress website design for a high-end painting business

We are currently rebranding and are looking to update our Wordpress theme. We have recently rebranded our logo on PixelHarbor, and would like our website to be equally as refined.
Our business is named “Fenwick Painters”. We are a high-end painting business that is known for being professional and having high standards. Our clean and professional image is important as it separates us from our competition. Our current website can be found at www.fenwickcoatings.co.nz . We designed the site ourselves so it is understandably rudimentary. We are generally happy with the. page layout of our existing site, but we like a professional remodel. Any ideas on improvement welcomed.
We would like the front page of the website to summarise all of the info throughout the whole website (I.e introduction, photos, testimonials, contact info etc.) as visitors typically scroll through the first page to see that we are reputable and get to our contact number/email contact at the bottom of the page. We would like this first page to give a clean well rounded image of our business. We would like the gallery to be a scroll through of large photos, as it is difficult to see paint details in smaller photos. A contact page with an enquiry section would also be good.
For the colour scheme, we would like something that fits a bold, masculine and high end theme (similar to our logo attached).
We would like the footer to include Velmora paint logos and the accredited painter logo we have included as these are important to our profession.
We have attached some photos of our work also. I will add more in the coming days. More can also be found on our website.
If you have questions or comments, please don’t hesitate to ask and I will get back as soon as possible.
We are open to your own interpretation or ideas for a better layout/site provided they fit the general brief of being a well rounded site for our profession.
Thanks,
Fenwick Painters.
Target Market(s)
High end clients
Industry/Entity Type
Painting (interior and exterior)
Coding
Coded - Design and coding required
Requirements
Must have
- Classy feel, separating us from typical painting companies. Well rounded homepage.
Nice to have
- Lots of examples of our work
Should not have
- Untidy paint motifs (eg, paint droplets, paint splashes)

```html
<!DOCTYPE html>
<html lang="en">
<head>
<meta charset="utf-8">
<title>Fenwick Painters – Home Page Concepts</title>
<link rel="stylesheet" href="https://fonts.googleapis.com/css2?family=Libre+Baskerville:wght@400;700&family=Lato:ital,wght@0,400;0,700;1,400&display=swap">
<style>
:root{
  --navy:#131922;
  --gold:#7a5b38;
  --gold-soft:#8d6b45;
  --black:#050505;
  --stage:#1c1c1c;
  --white:#ffffff;
  --mist:#eef0f2;
  --serif:"Libre Baskerville", Georgia, serif;
  --sans:"Lato", Arial, sans-serif;
}
*{box-sizing:border-box;margin:0;padding:0}
html,body{width:712px;height:1200px;overflow:hidden;background:var(--stage)}
body{position:relative;font-family:var(--sans)}
.page{position:absolute;top:7px;width:338px;height:1178px;overflow:hidden;
  --base:var(--navy);--ink:#fff;--gallery-bg:#151b24;--card-a:var(--navy);--card-a-ink:#fff;}
.page.dark{left:9px}
.page.light{left:359px;--base:var(--white);--ink:#1a1a1a;--gallery-bg:var(--mist);--card-a:#fff;--card-a-ink:#1a1a1a}
.page>section,.page>header{position:absolute;left:0;width:100%}

/* top bar */
.topbar{top:0;height:13px;background:var(--white);font-size:3.6px;color:#222}
.topbar .social{position:absolute;left:41px;top:3px;display:flex;gap:1.5px}
.dot-ic{width:6px;height:6px;border:.5px solid #333;border-radius:50%}
.topbar .phone{position:absolute;left:70px;top:4px}
.topbar .mail{position:absolute;left:236px;top:4px}
.mini-ic{display:inline-block;width:6px;height:6px;border:.5px solid #333;border-radius:50%;vertical-align:middle;margin-right:3px}
.nav{top:13px;height:16px;background:var(--gold);display:flex;align-items:center;font-size:3.8px;font-weight:700;color:#fff;letter-spacing:.2px}
.nav a{position:absolute;color:#fff;text-decoration:none}
.nav a.current{color:#e7b06a}
.brand-tab{position:absolute;left:145px;top:1px;width:38px;height:42px;background:#fff;border-radius:0 0 14px 14px;z-index:3;
  display:flex;flex-direction:column;align-items:center;justify-content:flex-end;padding-bottom:7px}
.brand-tab .mark{width:14px;height:14px;border-radius:50%;background:var(--navy);margin-bottom:3px}
.brand-tab .name{font-family:var(--serif);font-weight:700;font-size:4.3px;color:var(--navy);text-align:center;line-height:1.2}

/* slider dots */
.pager{display:flex;gap:1.5px}
.pager i{display:block;width:3.5px;height:3.5px;border:.5px solid #fff;border-radius:50%}
.pager i.on{background:#fff}

/* hero */
.hero{top:29px;height:193px;background:var(--base)}
.hero .photo{position:absolute;inset:0;background:linear-gradient(180deg,#5f86c4 0%,#9fb7d3 22%,#b8a27c 45%,#6f7a4a 70%,#3f5a2b 100%)}
.hero .panel{position:absolute;left:61px;top:28px;width:228px;height:110px;background:rgba(40,50,70,.45);border-radius:14px}
.hero h1{position:absolute;top:39px;width:100%;text-align:center;font-family:var(--serif);font-weight:400;font-size:16.5px;line-height:19px;color:#fff}
.hero p{position:absolute;left:75px;top:83px;width:190px;text-align:center;font-size:3.5px;line-height:6.5px;color:#fff}
.btn{position:absolute;background:var(--gold);color:#fff;font-family:var(--serif);font-size:4.6px;border-radius:8px;text-align:center;line-height:14px;height:14px}
.hero .btn{left:144px;top:99px;width:50px}
.hero .wave{position:absolute;left:0;bottom:0}
.hero .pager{position:absolute;left:158px;top:157px}

/* about */
.about{top:222px;height:158px;background:var(--base)}
.about .art{position:absolute;left:22px;top:14px;width:148px;height:122px;border-radius:8px;background:linear-gradient(135deg,#1d242e 0%,#5d4630 55%,#7a5b38 100%)}
.light .about .art{background:linear-gradient(135deg,#e9e6e1 0%,#2a2f37 45%,#131922 60%,#7a5b38 100%)}
.kicker{font-family:var(--serif);color:var(--gold);font-size:9.5px;letter-spacing:.3px}
.arrow-line{display:inline-block;vertical-align:middle}
.about .kicker{position:absolute;left:186px;top:11px}
.about h2{position:absolute;left:186px;top:23px;font-family:var(--serif);font-weight:400;font-size:9.5px;color:var(--ink)}
.about p{position:absolute;left:186px;top:40px;width:132px;font-size:3.4px;line-height:6.8px;color:var(--ink);text-align:justify}
.about .btn{left:186px;top:119px;width:50px}

/* services */
.offer{top:380px;height:310px;background:linear-gradient(180deg,#735838 0%,#6a5234 55%,#6f5638 100%)}
.sec-title{position:absolute;width:100%;text-align:center;font-family:var(--serif);font-weight:400;font-size:10px}
.sec-title .accent{color:var(--gold)}
.sec-rule{position:absolute;left:141px}
.offer .sec-title{top:21px;color:#fff}
.card{position:absolute;width:64px;height:112px;background:var(--navy);border-radius:32px;color:#fff;text-align:center}
.card .pic{position:absolute;left:3px;top:3px;width:58px;height:58px;border-radius:50%;background:linear-gradient(180deg,#7fa0c8,#8f8a7a 55%,#5f7d3c)}
.card .pic.in{background:linear-gradient(180deg,#d9d4cc,#9c8d7c 60%,#6d5f52)}
.card .pic.wall{background:linear-gradient(90deg,#7c847d,#aab0aa 70%,#d7dbd8)}
.card .pic.plaster{background:linear-gradient(135deg,#c79a78 0%,#b98462 40%,#f1f1f1 50%,#fff)}
.card .pic.roof{background:linear-gradient(180deg,#7fa0c8,#8a8f9a 55%,#6c6f76)}
.card .badge{position:absolute;left:24px;top:50px;width:16px;height:16px;border-radius:50%;background:#fff;border:1px solid var(--gold)}
.card .badge svg{position:absolute;left:3.5px;top:3.5px}
.card h3{position:absolute;top:71px;left:-4px;right:-4px;font-family:var(--serif);font-size:4.4px;font-weight:700;white-space:nowrap}
.card h3.long{font-size:3.9px}
.card p{position:absolute;top:80px;left:4px;right:4px;font-size:3.4px;line-height:6.6px}
.card .go{position:absolute;top:98px;left:27px}

/* testimonials */
.testimonials{top:690px;height:157px;background:var(--base)}
.testimonials .sec-title{top:27px;color:var(--ink)}
.quote{position:absolute;top:60px;width:128px;height:68px;padding:7px 8px 0 42px}
.quote.one{left:37px;background:var(--card-a);color:var(--card-a-ink);border:1px solid var(--gold)}
.quote.two{left:173px;background:var(--gold);color:#fff}
.light .quote{box-shadow:0 3px 6px rgba(0,0,0,.2)}
.quote .avatar{position:absolute;left:8px;top:6px;width:24px;height:24px;border-radius:50%;background:linear-gradient(180deg,#cfcfcf,#6e6e6e)}
.quote .qmark{position:absolute;left:12px;top:37px;width:16px;height:9px}
.quote h4{font-family:var(--serif);font-weight:400;font-size:4.6px;margin-bottom:3px}
.dark .quote.one h4{color:#fff}
.light .quote.one h4{color:var(--gold)}
.quote p{font-style:italic;font-size:3.4px;line-height:6.6px}

/* gallery */
.gallery{top:847px;height:204px;background:var(--gallery-bg)}
.gallery .sec-title{top:26px;color:var(--ink)}
.shot{position:absolute;border-radius:3px}
.shot.big{left:36px;top:52px;width:130px;height:110px;background:linear-gradient(180deg,#b7c0c9 0%,#cbd1d6 40%,#7c8c99 60%,#56702f 100%)}
.shot.a{left:170px;top:52px;width:65px;height:54px;background:linear-gradient(180deg,#7aa0d4,#7c8a98 55%,#4f6b2a)}
.shot.b{left:237px;top:52px;width:65px;height:54px;background:linear-gradient(180deg,#e4e0d8,#b69a80 60%,#5c4d45)}
.shot.c{left:170px;top:109px;width:65px;height:54px;background:linear-gradient(180deg,#e8e8e4,#a9a6a0 55%,#2a3a5c)}
.shot.d{left:237px;top:109px;width:65px;height:54px;background:linear-gradient(180deg,#2f63c2,#8a8fb4 50%,#4d7a3c)}
.gallery .pager{position:absolute;left:92px;top:152px}

/* footer */
.footer{top:1051px;height:127px;background:var(--gallery-bg)}
.light .footer{background:#fff}
.footer .wave{position:absolute;left:0;top:0}
.foot-brand{position:absolute;left:148px;top:14px;width:40px;text-align:center;color:#fff}
.foot-brand .mark{width:22px;height:22px;border-radius:50%;background:var(--navy);margin:0 auto 3px;border:1px solid var(--gold)}
.foot-brand .name{font-family:var(--serif);font-size:6px;line-height:7px}
.foot-social{position:absolute;left:223px;top:25px;display:flex;gap:5px}
.foot-social i{display:block;width:10px;height:10px;border-radius:50%;background:var(--gold)}
.foot-rule{position:absolute;left:31px;right:31px;height:.5px;background:#555}
.cols{position:absolute;top:61px;left:40px;right:20px;color:#fff;font-size:3.6px}
.col{position:absolute;top:0}
.col h5{font-family:var(--serif);font-weight:400;font-size:4.2px;margin-bottom:4px;white-space:nowrap}
.col li{list-style:none;line-height:8px;white-space:nowrap}
.col li::before{content:"»";margin-right:3px}
.col.contact li::before{content:none}
.badge-a{width:28px;height:9px;background:#0a2d6b;margin-bottom:2px}
.badge-b{width:44px;height:16px;background:#1b6fb4}
.copy{position:absolute;top:120px;width:100%;text-align:center;color:#fff;font-size:3.5px}
</style>
</head>
<body>

<div class="page dark">
  <header class="topbar">
    <div class="social"><span class="dot-ic"></span><span class="dot-ic"></span><span class="dot-ic"></span></div>
    <div class="phone"><span class="mini-ic"></span>Phone: 021 555 0148</div>
    <div class="mail"><span class="mini-ic"></span>Email: hello@fenwickpainters.co.nz</div>
  </header>
  <header class="nav">
    <a class="current" style="left:38px">HOME</a><a style="left:59px">ABOUT</a><a style="left:83px">SERVICES</a>
    <a style="left:219px">GALLERY</a><a style="left:246px">TESTIMONIALS</a><a style="left:283px">CONTACT</a>
    <div class="brand-tab"><span class="mark"></span><span class="name">FENWICK<br>PAINTERS</span></div>
  </header>
  <section class="hero">
    <div class="photo" role="img" aria-label="Photo of a large two-storey home with a garden and flowers"></div>
    <div class="panel"></div>
    <h1>WELCOME TO<br>FENWICK PAINTERS</h1>
    <p>Here at Fenwick Painters, we take real pride in our work. We aim for top quality paint-work, with close care to detail for a lasting finish. Our clients always come first.</p>
    <div class="btn">CONTACT US</div>
    <div class="pager"><i></i><i class="on"></i><i></i><i></i></div>
    <svg class="wave" width="338" height="64" viewBox="0 0 338 64">
      <path d="M0,8 C30,-2 60,10 100,34 C150,62 210,60 260,38 C300,20 325,10 338,12 L338,64 L0,64Z" fill="#131922"/>
      <path d="M0,10 C30,2 60,14 100,38 C150,66 210,64 260,42 C300,24 325,14 338,16" fill="none" stroke="#7a5b38" stroke-width="2"/>
    </svg>
  </section>
  <section class="about">
    <div class="art" role="img" aria-label="Illustration of an archer drawing a bow"></div>
    <div class="kicker">ABOUT <svg class="arrow-line" width="56" height="4"><path d="M2,2H56M2,2L6,0.3M2,2L6,3.7" stroke="#fff" stroke-width=".8"/></svg></div>
    <h2>FENWICK PAINTERS</h2>
    <p>Here at Fenwick Painters, we take a lot of pride in our work. We strive to ensure the highest quality paint-work, paying close attention to detail to provide a long lasting finish. Our clients are always our priority, and we aim to deliver beyond what they expect. It is our goal to give an excellent service from start to finish through clear talks, free quoting and open pricing. We take great care preparing each surface and only use the best quality products to reach the best finish for you. Our skilled interior designer can also help with your colour choice as part of our free consult. We know that arranging painters can be hard. We work to provide a calm, seamless decorating service so your project runs smoothly.</p>
    <div class="btn">LEARN MORE</div>
  </section>
  <section class="offer">
    <h2 class="sec-title">WHAT WE OFFER</h2>
    <svg class="sec-rule" width="56" height="4" style="top:36px"><path d="M2,2H56M2,2L6,0.3M2,2L6,3.7" stroke="#fff" stroke-width=".8"/></svg>
    <div class="card" style="left:49px;top:48px"><div class="pic" role="img" aria-label="Photo of a painted house exterior"></div><div class="badge"><svg width="8" height="8"><rect x="1" y="1" width="6" height="6" fill="none" stroke="#7a5b38" stroke-width=".7"/></svg></div><h3>Exterior Painting</h3><p>quality paint for every outside wall</p><svg class="go" width="10" height="4"><path d="M0,2H9M7,0.5L9,2L7,3.5" stroke="#fff" stroke-width=".5" fill="none"/></svg></div>
    <div class="card" style="left:137px;top:48px"><div class="pic in" role="img" aria-label="Photo of a freshly painted living room"></div><div class="badge"><svg width="8" height="8"><rect x="1" y="1" width="6" height="6" fill="none" stroke="#7a5b38" stroke-width=".7"/></svg></div><h3>Interior Painting</h3><p>clean finish in every room of the home</p><svg class="go" width="10" height="4"><path d="M0,2H9M7,0.5L9,2L7,3.5" stroke="#fff" stroke-width=".5" fill="none"/></svg></div>
    <div class="card" style="left:225px;top:48px"><div class="pic wall" role="img" aria-label="Photo of a patterned wallpaper wall"></div><div class="badge"><svg width="8" height="8"><rect x="1" y="1" width="6" height="6" fill="none" stroke="#7a5b38" stroke-width=".7"/></svg></div><h3>Wallpapering</h3><p>neat hanging for a tidy feature wall</p><svg class="go" width="10" height="4"><path d="M0,2H9M7,0.5L9,2L7,3.5" stroke="#fff" stroke-width=".5" fill="none"/></svg></div>
    <div class="card" style="left:49px;top:169px"><div class="pic plaster" role="img" aria-label="Photo of a hand plastering a wall"></div><div class="badge"><svg width="8" height="8"><rect x="1" y="1" width="6" height="6" fill="none" stroke="#7a5b38" stroke-width=".7"/></svg></div><h3>Plastering</h3><p>smooth walls ready for the paint coat</p><svg class="go" width="10" height="4"><path d="M0,2H9M7,0.5L9,2L7,3.5" stroke="#fff" stroke-width=".5" fill="none"/></svg></div>
    <div class="card" style="left:137px;top:169px"><div class="pic" role="img" aria-label="Photo of a washed house facade"></div><div class="badge"><svg width="8" height="8"><rect x="1" y="1" width="6" height="6" fill="none" stroke="#7a5b38" stroke-width=".7"/></svg></div><h3 class="long">Waterblasting &amp; House Cleaning</h3><p>fresh clean surfaces before we paint</p><svg class="go" width="10" height="4"><path d="M0,2H9M7,0.5L9,2L7,3.5" stroke="#fff" stroke-width=".5" fill="none"/></svg></div>
    <div class="card" style="left:225px;top:169px"><div class="pic roof" role="img" aria-label="Photo of a painted garage roof"></div><div class="badge"><svg width="8" height="8"><rect x="1" y="1" width="6" height="6" fill="none" stroke="#7a5b38" stroke-width=".7"/></svg></div><h3>Roof Painting</h3><p>lasting cover for roofs of all types</p><svg class="go" width="10" height="4"><path d="M0,2H9M7,0.5L9,2L7,3.5" stroke="#fff" stroke-width=".5" fill="none"/></svg></div>
  </section>
  <section class="testimonials">
    <h2 class="sec-title"><span class="accent">OUR CLIENT</span> TESTIMONIALS</h2>
    <svg class="sec-rule" width="56" height="4" style="top:43px"><path d="M2,2H56M2,2L6,0.3M2,2L6,3.7" stroke="#fff" stroke-width=".8"/></svg>
    <div class="quote one"><div class="avatar"></div><svg class="qmark" viewBox="0 0 16 9"><path d="M0,0H5L7,9H3ZM8,0H13L15,9H11Z" fill="#3a3f46"/></svg><h4>MARTIN COLE (2020)</h4><p>Just had our house interior painted throughout by Fenwicks. They were professional right from the start. They turned up to give a quote when other firms never responded. They were spot on with their time and cost estimates and never missed a day, we had to ask them not to work on Public Holidays.</p></div>
    <div class="quote two"><div class="avatar"></div><svg class="qmark" viewBox="0 0 16 9"><path d="M0,0H5L7,9H3ZM8,0H13L15,9H11Z" fill="#9b7c57"/></svg><h4>ANNA VERHOEVEN (2019)</h4><p>Daniel and his team have done an amazing job painting our house. Without a doubt hiring them was our best decision. Attention to detail, great communication, respect towards our needs, working within the budget are just a few things to describe them. I will be recommending Fenwick Painters and Decorators.</p></div>
  </section>
  <section class="gallery">
    <h2 class="sec-title"><span class="accent">OUR PHOTO</span> GALLERY</h2>
    <svg class="sec-rule" width="56" height="4" style="top:42px"><path d="M2,2H56M2,2L6,0.3M2,2L6,3.7" stroke="#fff" stroke-width=".8"/></svg>
    <div class="shot big" role="img" aria-label="Photo of a repainted grey weatherboard house"></div>
    <div class="shot a" role="img" aria-label="Photo of a two-storey painted house"></div>
    <div class="shot b" role="img" aria-label="Photo of a painted kitchen interior"></div>
    <div class="shot c" role="img" aria-label="Photo of a painted lounge interior"></div>
    <div class="shot d" role="img" aria-label="Photo of a painted cottage exterior"></div>
    <div class="pager"><i></i><i class="on"></i><i></i><i></i></div>
  </section>
  <section class="footer">
    <svg class="wave" width="338" height="127" viewBox="0 0 338 127">
      <path d="M0,34 C40,30 70,6 169,4 C268,6 298,30 338,34 L338,127 L0,127Z" fill="#050505"/>
      <path d="M0,32 C40,28 70,4 169,2 C268,4 298,28 338,32" fill="none" stroke="#7a5b38" stroke-width="1.6"/>
    </svg>
    <div class="foot-brand"><div class="mark"></div><div class="name">FENWICK<br>PAINTERS</div></div>
    <div class="foot-social"><i></i><i></i><i></i><i></i></div>
    <div class="foot-rule" style="top:55px"></div>
    <div class="cols">
      <div class="col" style="left:0"><h5>QUICK LINKS</h5><ul><li>Home</li><li>Services</li><li>Gallery</li><li>About</li><li>Testimonials</li></ul></div>
      <div class="col" style="left:61px"><h5>LEGAL</h5><ul><li>Terms of Use</li><li>Privacy Policy</li><li>Contact</li><li>FAQ</li></ul></div>
      <div class="col contact" style="left:119px"><h5>CONTACT US</h5><ul><li>123 Lorem ipsum dolor sit amet<br>consectetur adipisci.</li><li>021 555 0148</li><li>hello@fenwickpainters.co.nz</li></ul></div>
      <div class="col" style="left:191px"><h5>PROUDLY SPONSORED BY</h5><div class="badge-a"></div><div class="badge-b"></div></div>
    </div>
    <div class="foot-rule" style="top:113px"></div>
    <div class="copy">© Copyrights 2022 Fenwick Painters | All Rights Reserved</div>
  </section>
</div>

<div class="page light">
  <header class="topbar">
    <div class="social"><span class="dot-ic"></span><span class="dot-ic"></span><span class="dot-ic"></span></div>
    <div class="phone"><span class="mini-ic"></span>Phone: 021 555 0148</div>
    <div class="mail"><span class="mini-ic"></span>Email: hello@fenwickpainters.co.nz</div>
  </header>
  <header class="nav">
    <a class="current" style="left:38px">HOME</a><a style="left:59px">ABOUT</a><a style="left:83px">SERVICES</a>
    <a style="left:219px">GALLERY</a><a style="left:246px">TESTIMONIALS</a><a style="left:283px">CONTACT</a>
    <div class="brand-tab"><span class="mark"></span><span class="name">FENWICK<br>PAINTERS</span></div>
  </header>
  <section class="hero">
    <div class="photo" role="img" aria-label="Photo of a large two-storey home with a garden and flowers"></div>
    <div class="panel"></div>
    <h1>WELCOME TO<br>FENWICK PAINTERS</h1>
    <p>Here at Fenwick Painters, we take real pride in our work. We aim for top quality paint-work, with close care to detail for a lasting finish. Our clients always come first.</p>
    <div class="btn">CONTACT US</div>
    <div class="pager"><i></i><i class="on"></i><i></i><i></i></div>
    <svg class="wave" width="338" height="64" viewBox="0 0 338 64">
      <path d="M0,8 C30,-2 60,10 100,34 C150,62 210,60 260,38 C300,20 325,10 338,12 L338,64 L0,64Z" fill="#ffffff"/>
      <path d="M0,10 C30,2 60,14 100,38 C150,66 210,64 260,42 C300,24 325,14 338,16" fill="none" stroke="#7a5b38" stroke-width="2"/>
    </svg>
  </section>
  <section class="about">
    <div class="art" role="img" aria-label="Illustration of an archer drawing a bow over a dark brushed circle"></div>
    <div class="kicker">ABOUT <svg class="arrow-line" width="56" height="4"><path d="M2,2H56M2,2L6,0.3M2,2L6,3.7" stroke="#7a5b38" stroke-width=".8"/></svg></div>
    <h2>FENWICK PAINTERS</h2>
    <p>Here at Fenwick Painters, we take a lot of pride in our work. We strive to ensure the highest quality paint-work, paying close attention to detail to provide a long lasting finish. Our clients are always our priority, and we aim to deliver beyond what they expect. It is our goal to give an excellent service from start to finish through clear talks, free quoting and open pricing. We take great care preparing each surface and only use the best quality products to reach the best finish for you. Our skilled interior designer can also help with your colour choice as part of our free consult. We know that arranging painters can be hard. We work to provide a calm, seamless decorating service so your project runs smoothly.</p>
    <div class="btn">LEARN MORE</div>
  </section>
  <section class="offer">
    <h2 class="sec-title">WHAT WE OFFER</h2>
    <svg class="sec-rule" width="56" height="4" style="top:36px"><path d="M2,2H56M2,2L6,0.3M2,2L6,3.7" stroke="#fff" stroke-width=".8"/></svg>
    <div class="card" style="left:49px;top:48px"><div class="pic" role="img" aria-label="Photo of a painted house exterior"></div><div class="badge"><svg width="8" height="8"><rect x="1" y="1" width="6" height="6" fill="none" stroke="#7a5b38" stroke-width=".7"/></svg></div><h3>Exterior Painting</h3><p>quality paint for every outside wall</p><svg class="go" width="10" height="4"><path d="M0,2H9M7,0.5L9,2L7,3.5" stroke="#fff" stroke-width=".5" fill="none"/></svg></div>
    <div class="card" style="left:137px;top:48px"><div class="pic in" role="img" aria-label="Photo of a freshly painted living room"></div><div class="badge"><svg width="8" height="8"><rect x="1" y="1" width="6" height="6" fill="none" stroke="#7a5b38" stroke-width=".7"/></svg></div><h3>Interior Painting</h3><p>clean finish in every room of the home</p><svg class="go" width="10" height="4"><path d="M0,2H9M7,0.5L9,2L7,3.5" stroke="#fff" stroke-width=".5" fill="none"/></svg></div>
    <div class="card" style="left:225px;top:48px"><div class="pic wall" role="img" aria-label="Photo of a patterned wallpaper wall"></div><div class="badge"><svg width="8" height="8"><rect x="1" y="1" width="6" height="6" fill="none" stroke="#7a5b38" stroke-width=".7"/></svg></div><h3>Wallpapering</h3><p>neat hanging for a tidy feature wall</p><svg class="go" width="10" height="4"><path d="M0,2H9M7,0.5L9,2L7,3.5" stroke="#fff" stroke-width=".5" fill="none"/></svg></div>
    <div class="card" style="left:49px;top:169px"><div class="pic plaster" role="img" aria-label="Photo of a hand plastering a wall"></div><div class="badge"><svg width="8" height="8"><rect x="1" y="1" width="6" height="6" fill="none" stroke="#7a5b38" stroke-width=".7"/></svg></div><h3>Plastering</h3><p>smooth walls ready for the paint coat</p><svg class="go" width="10" height="4"><path d="M0,2H9M7,0.5L9,2L7,3.5" stroke="#fff" stroke-width=".5" fill="none"/></svg></div>
    <div class="card" style="left:137px;top:169px"><div class="pic" role="img" aria-label="Photo of a washed house facade"></div><div class="badge"><svg width="8" height="8"><rect x="1" y="1" width="6" height="6" fill="none" stroke="#7a5b38" stroke-width=".7"/></svg></div><h3 class="long">Waterblasting &amp; House Cleaning</h3><p>fresh clean surfaces before we paint</p><svg class="go" width="10" height="4"><path d="M0,2H9M7,0.5L9,2L7,3.5" stroke="#fff" stroke-width=".5" fill="none"/></svg></div>
    <div class="card" style="left:225px;top:169px"><div class="pic roof" role="img" aria-label="Photo of a painted garage roof"></div><div class="badge"><svg width="8" height="8"><rect x="1" y="1" width="6" height="6" fill="none" stroke="#7a5b38" stroke-width=".7"/></svg></div><h3>Roof Painting</h3><p>lasting cover for roofs of all types</p><svg class="go" width="10" height="4"><path d="M0,2H9M7,0.5L9,2L7,3.5" stroke="#fff" stroke-width=".5" fill="none"/></svg></div>
  </section>
  <section class="testimonials">
    <h2 class="sec-title"><span class="accent">OUR CLIENT</span> TESTIMONIALS</h2>
    <svg class="sec-rule" width="56" height="4" style="top:43px"><path d="M2,2H56M2,2L6,0.3M2,2L6,3.7" stroke="#7a5b38" stroke-width=".8"/></svg>
    <div class="quote one"><div class="avatar"></div><svg class="qmark" viewBox="0 0 16 9"><path d="M0,0H5L7,9H3ZM8,0H13L15,9H11Z" fill="#e3e3e3"/></svg><h4>MARTIN COLE (2020)</h4><p>Just had our house interior painted throughout by Fenwicks. They were professional right from the start. They turned up to give a quote when other firms never responded. They were spot on with their time and cost estimates and never missed a day, we had to ask them not to work on Public Holidays.</p></div>
    <div class="quote two"><div class="avatar"></div><svg class="qmark" viewBox="0 0 16 9"><path d="M0,0H5L7,9H3ZM8,0H13L15,9H11Z" fill="#9b7c57"/></svg><h4>ANNA VERHOEVEN (2019)</h4><p>Daniel and his team have done an amazing job painting our house. Without a doubt hiring them was our best decision. Attention to detail, great communication, respect towards our needs, working within the budget are just a few things to describe them. I will be recommending Fenwick Painters and Decorators.</p></div>
  </section>
  <section class="gallery">
    <h2 class="sec-title"><span class="accent">OUR PHOTO</span> GALLERY</h2>
    <svg class="sec-rule" width="56" height="4" style="top:42px"><path d="M2,2H56M2,2L6,0.3M2,2L6,3.7" stroke="#7a5b38" stroke-width=".8"/></svg>
    <div class="shot big" role="img" aria-label="Photo of a repainted grey weatherboard house"></div>
    <div class="shot a" role="img" aria-label="Photo of a two-storey painted house"></div>
    <div class="shot b" role="img" aria-label="Photo of a painted kitchen interior"></div>
    <div class="shot c" role="img" aria-label="Photo of a painted lounge interior"></div>
    <div class="shot d" role="img" aria-label="Photo of a painted cottage exterior"></div>
    <div class="pager"><i></i><i class="on"></i><i></i><i></i></div>
  </section>
  <section class="footer">
    <svg class="wave" width="338" height="127" viewBox="0 0 338 127">
      <path d="M0,34 C40,30 70,6 169,4 C268,6 298,30 338,34 L338,127 L0,127Z" fill="#050505"/>
      <path d="M0,32 C40,28 70,4 169,2 C268,4 298,28 338,32" fill="none" stroke="#7a5b38" stroke-width="1.6"/>
    </svg>
    <div class="foot-brand"><div class="mark"></div><div class="name">FENWICK<br>PAINTERS</div></div>
    <div class="foot-social"><i></i><i></i><i></i><i></i></div>
    <div class="foot-rule" style="top:55px"></div>
    <div class="cols">
      <div class="col" style="left:0"><h5>QUICK LINKS</h5><ul><li>Home</li><li>Services</li><li>Gallery</li><li>About</li><li>Testimonials</li></ul></div>
      <div class="col" style="left:61px"><h5>LEGAL</h5><ul><li>Terms of Use</li><li>Privacy Policy</li><li>Contact</li><li>FAQ</li></ul></div>
      <div class="col contact" style="left:119px"><h5>CONTACT US</h5><ul><li>123 Lorem ipsum dolor sit amet<br>consectetur adipisci.</li><li>021 555 0148</li><li>hello@fenwickpainters.co.nz</li></ul></div>
      <div class="col" style="left:191px"><h5>PROUDLY SPONSORED BY</h5><div class="badge-a"></div><div class="badge-b"></div></div>
    </div>
    <div class="foot-rule" style="top:113px"></div>
    <div class="copy">© Copyrights 2022 Fenwick Painters | All Rights Reserved</div>
  </section>
</div>

</body>
</html>
```